The Velvet Magpie business card

I need a business card for my makeup artist business. I specialise in bridal, glamour, formal and special occasion makeup.
I am a mobile makeup artist who caters for every from nowra to sydney.
I do the following services:
Bridal makeup
airbrush makeup
special occasion
formals
hens nights/ girls night
makeup lesson
makeup for all ages from flower girl to Nanna of the bride!
photoshoot makeup
SPFX

I would like the card to portray a very professional sleek makeup business. I would also like another version of the card directed especially towards brides.

Please see my website to understand colours etc www.thevelvetmagpie-example.com

The Velvet Magpie
Professional Makeup Artist
Lorraine Kedby
0491802643
info@thevelvetmagpie-example.com
www.thevelvetmagpie-example.com
www.facebook.com/thevelvetmagpie

```html
<!DOCTYPE html>
<html lang="en">
<head>
<meta charset="utf-8">
<title>The Velvet Magpie – Business Card</title>
<link rel="stylesheet" href="https://fonts.googleapis.com/css2?family=Open+Sans:wght@400;600;700&family=Oswald:wght@600&display=swap">
<style>
  :root {
    --magenta: #e0288f;
    --magenta-deep: #c81a7a;
    --magenta-light: #ee4aa6;
    --charcoal: #4b4b4e;
    --silver: #d9d9d9;
    --paper: #ffffff;
    --ink: #1e1e22;
    --stage: #ecebea;
    --photo-navy: #2f3a6b;
    --photo-slate: #5b5f6e;
    --photo-green: #8fa770;
  }
  * { box-sizing: border-box; margin: 0; padding: 0; }
  html, body { width: 1200px; height: 913px; overflow: hidden; }
  body {
    background: var(--stage);
    font-family: "Open Sans", Arial, sans-serif;
    position: relative;
  }
  .card {
    position: absolute;
    top: 308px;
    width: 520px;
    height: 297px;
    overflow: hidden;
    box-shadow: 0 6px 18px rgba(0,0,0,.18);
  }
  .card--front { left: 60px; }
  .card--back { left: 620px; }
  .card__shapes { position: absolute; inset: 0; }

  .brand-name {
    position: absolute;
    left: 24px;
    top: 118px;
    height: 34px;
    line-height: 34px;
    font-size: 26px;
    font-weight: 600;
    letter-spacing: 1px;
    white-space: nowrap;
    text-transform: uppercase;
    color: var(--magenta);
    transform: rotate(-22.3deg);
    transform-origin: left bottom;
  }

  .contact {
    position: absolute;
    left: 26px; top: 174px;
    color: var(--paper);
  }
  .contact__name { font-size: 20px; font-weight: 700; line-height: 24px; }
  .contact__role {
    font-size: 13px; font-weight: 400; line-height: 18px;
    padding-bottom: 5px;
    border-bottom: 1.5px solid var(--paper);
    width: 210px;
    margin-bottom: 8px;
  }
  .contact__list { list-style: none; font-size: 12.5px; }
  .contact__list li { display: flex; align-items: center; gap: 9px; height: 20px; }
  .contact__list svg { width: 14px; height: 14px; flex: none; }

  .social {
    position: absolute;
    right: 20px; bottom: 22px;
    display: flex; flex-direction: column; align-items: flex-end; gap: 8px;
    color: var(--paper);
    font-size: 12px;
  }
  .social__mark { width: 12px; height: 12px; background: var(--magenta); }

  .photo {
    position: absolute; inset: 0;
    background: linear-gradient(160deg, var(--photo-slate) 0%, var(--photo-navy) 45%, #3d4a80 65%, var(--photo-green) 100%);
  }
  .services {
    position: absolute;
    left: 0; right: 0; top: 178px;
    height: 86px;
    background: linear-gradient(90deg, rgba(200,26,122,.92), rgba(238,74,166,.85));
    padding: 9px 16px;
    font-family: "Oswald", "Arial Narrow", sans-serif;
    font-weight: 600;
    font-size: 13px;
    line-height: 1.5;
    color: var(--ink);
  }
</style>
</head>
<body>

  <section class="card card--front" aria-label="Business card front">
    <svg class="card__shapes" viewBox="0 0 520 297" preserveAspectRatio="none" aria-hidden="true">
      <defs>
        <linearGradient id="magentaFill" x1="0" y1="0" x2="0" y2="1">
          <stop offset="0" stop-color="#ee4aa6"/>
          <stop offset="1" stop-color="#c81a7a"/>
        </linearGradient>
      </defs>
      <rect width="520" height="297" fill="#4b4b4e"/>
      <polygon points="0,0 380,0 380,22 0,178" fill="#ffffff"/>
      <polygon points="0,178 380,22 380,297 0,297" fill="url(#magentaFill)"/>
      <polygon points="300,0 380,0 380,5 312,5" fill="#e0288f"/>
      <rect x="380" y="0" width="8" height="297" fill="#d9d9d9"/>
    </svg>

    <div class="brand-name">The Velvet Magpie</div>

    <div class="contact">
      <p class="contact__name">Lorraine Kedby</p>
      <p class="contact__role">Professional Makeup Artist</p>
      <ul class="contact__list">
        <li>
          <svg viewBox="0 0 16 16" aria-hidden="true"><path fill="#fff" d="M3 1h3l1.5 4-2 1.2a9 9 0 0 0 4.3 4.3L11 8.5l4 1.5v3a2 2 0 0 1-2 2A12 12 0 0 1 1 3a2 2 0 0 1 2-2z"/></svg>
          0491802643
        </li>
        <li>
          <svg viewBox="0 0 16 16" aria-hidden="true"><rect x="1" y="3" width="14" height="10" fill="#fff"/><path d="M1 3l7 6 7-6" stroke="#e0288f" stroke-width="1.3" fill="none"/></svg>
          info@thevelvetmagpie-example.com
        </li>
        <li>
          <svg viewBox="0 0 16 16" aria-hidden="true"><circle cx="8" cy="8" r="7" fill="#fff"/><path d="M1 8h14M8 1c-3 4-3 10 0 14M8 1c3 4 3 10 0 14" stroke="#e0288f" stroke-width="1" fill="none"/></svg>
          www.thevelvetmagpie-example.com
        </li>
      </ul>
    </div>

    <div class="social">
      <span class="social__mark" aria-hidden="true"></span>
      <span>/thevelvetmagpie</span>
    </div>
  </section>

  <section class="card card--back" aria-label="Business card back">
    <div class="photo" role="img" aria-label="Photograph of a bridal party in navy dresses holding white bouquets"></div>
    <p class="services">
      Bridal makeup • Airbrush makeup • Special occasion • Formals<br>
      • Hens nights/ Girls night • Makeup lesson • Makeup for all ages from flower<br>
      girl to Nanna of the bride! • Photoshoot makeup • SPFX
    </p>
  </section>

</body>
</html>
```